Bring me business with this creative business card

Design my new business card. I am looking for something different with an impact. People will take a look at this card & they will 1- see how different & creative I am, 2-understand what I do 3- Call me to meet me!

I make videos with a message, testimonials. I am dynamic, fun, creative & human. My new website is in construction but in the meantime you can check this old one: brightpath.ca & another one Tidebloom.com & tidebloom facebook page.
I make videos. sometimes with a cameraman, sometimes with my phone. As an ex Public Relations agent, the message is the most important thing for me. I want to make my clients shine! When they start with me they often remind me of a lamb, when I finish coaching them they are powerful like LIONS! That's why I need a powerful business card!

Target Market(s)

Entrepreneurs, solo entrepreneurs, small & medium companies & start ups. People i will meet while networking. People that need videos on their website & social Networks to get attention, to be visible. men & women. From 35 to 49 years old.
I am an ex Public relations agent. I used to send clients in traditional medias, now with videos they have more chances to be seen on google the new media. I do videos of the president, his team, his loyal clients saying how great the company is & expert videos like series so people can be seen for example every 1 st of every month with a short 2 minute video. Also with my 20 years in marketing & communications I can coach & give tips to anybody who needs it.
Target: anybody who would like my old website brightpath.ca & I also have another website but it will be off line soon: tidebloom.com could give you ideas.

Industry/Entity Type

Communications

Contact Information for Business Card

I am in Montreal,So the business cards have to be the usual size like we have in Montreal: 9 cm x 5 cm
Details:My text: Mathilde Tessier Communication coach/Lead Voice. "Creating Videos as unique as you" off: 514-555-0147 cell: 514-555-0183. tidebloom.com
mathilde@tidebloom.com logo facebook, youtube, instagram

Colors
f37122

Requirements
Must have
• Dynamic, happy. Orange. Be creative in the look but NOT the shape of the card. Easy to read. Big enough to read.
Should not have
• No funny shapes: no round, no square, just the usual. I love creative but NOT on shape.

```html
<!DOCTYPE html>
<html lang="en">
<head>
<meta charset="utf-8">
<title>Tidebloom Business Card</title>
<link rel="stylesheet" href="https://fonts.googleapis.com/css2?family=Cinzel:wght@700&family=Source+Sans+3:wght@400&family=Tinos:wght@700&display=swap">
<style>
  :root {
    --backdrop: #303030;
    --orange: #f37122;
    --orange-deep: #ee5a1c;
    --orange-warm: #f7941d;
    --amber: #fbb03b;
    --paper: #ffffff;
    --ink: #1e1e1e;
  }
  * { margin: 0; padding: 0; box-sizing: border-box; }
  html, body { width: 1200px; height: 900px; overflow: hidden; }
  body { background: var(--backdrop); position: relative; font-family: "Source Sans 3", sans-serif; }

  .card { position: absolute; top: 170px; width: 347px; height: 561px; }
  .card--front { left: 259px; background: linear-gradient(160deg, var(--orange-warm), var(--orange) 55%, var(--orange-warm)); }
  .card--back { left: 631px; background: var(--paper); }

  .card__face {
    position: absolute; left: 14px; top: 14px; width: 320px; height: 534px;
  }
  .card--front .card__face { background: var(--paper); text-align: center; }
  .card--back .card__face {
    background:
      radial-gradient(ellipse at 50% 45%, var(--amber) 0%, var(--orange-warm) 45%, var(--orange) 80%, var(--orange-deep) 100%);
  }

  .brand-mark {
    position: absolute; left: 110px; top: 58px; width: 100px; height: 100px;
    border-radius: 50%; background: var(--orange);
  }
  .brand-name {
    position: absolute; left: 0; right: 0; top: 192px;
    font-family: "Cinzel", serif; font-weight: 700; font-size: 33px;
    letter-spacing: 0.5px; color: var(--orange); line-height: 1;
  }
  .tagline {
    position: absolute; left: 0; right: 0; top: 229px;
    display: flex; align-items: center; justify-content: center; gap: 6px;
    font-size: 15px; color: var(--orange); line-height: 1;
  }
  .tagline::before, .tagline::after {
    content: ""; width: 30px; height: 1.5px; background: var(--orange-warm);
  }

  .person-name {
    position: absolute; left: 0; right: 0; top: 328px;
    font-family: "Tinos", serif; font-weight: 700; font-size: 21px;
    color: var(--orange-deep); letter-spacing: 0.3px;
  }
  .person-role {
    position: absolute; left: 0; right: 0; top: 352px;
    font-size: 15.5px; color: var(--ink);
  }
  .divider {
    position: absolute; left: 74px; top: 389px; width: 172px; height: 1.5px;
    background: var(--orange);
  }
  .contact-icons {
    position: absolute; left: 0; right: 0; top: 412px;
    display: flex; justify-content: center; gap: 3px;
  }
  .contact-icons svg { width: 17px; height: 17px; }
  .contact-list {
    position: absolute; left: 0; right: 0; top: 430px;
    list-style: none; font-size: 15.5px; line-height: 20px; color: var(--ink);
  }
</style>
</head>
<body>
  <section class="card card--front" aria-label="Business card front">
    <div class="card__face">
      <div class="brand-mark"></div>
      <div class="brand-name">TIDEBLOOM</div>
      <div class="tagline">1 FILM&nbsp;&nbsp;1 PURPOSE</div>

      <div class="person-name">MATHILDE TESSIER</div>
      <div class="person-role">Communication Coach/Lead Voice</div>
      <div class="divider"></div>

      <div class="contact-icons">
        <svg viewBox="0 0 20 20" aria-label="Office phone"><circle cx="10" cy="10" r="10" fill="var(--orange)"/><path d="M5 8c0-2 10-2 10 0v1h-3V8H8v1H5z M6 10h8l1 4H5z" fill="#fff"/></svg>
        <svg viewBox="0 0 20 20" aria-label="Cell phone"><circle cx="10" cy="10" r="10" fill="var(--orange)"/><rect x="7" y="4.5" width="6" height="11" rx="1" fill="#fff"/><rect x="8" y="6" width="4" height="7" fill="var(--orange)"/></svg>
        <svg viewBox="0 0 20 20" aria-label="Email"><circle cx="10" cy="10" r="10" fill="var(--orange)"/><rect x="5" y="6.5" width="10" height="7" fill="#fff"/><path d="M5 6.5l5 4 5-4" fill="none" stroke="var(--orange)" stroke-width="1"/></svg>
        <svg viewBox="0 0 20 20" aria-label="Website"><circle cx="10" cy="10" r="10" fill="var(--orange)"/><circle cx="10" cy="10" r="5" fill="none" stroke="#fff" stroke-width="1.3"/><path d="M5 10h10M10 5c-2.5 3-2.5 7 0 10M10 5c2.5 3 2.5 7 0 10" fill="none" stroke="#fff" stroke-width="1"/></svg>
      </div>
      <ul class="contact-list">
        <li>514-555-0147</li>
        <li>514-555-0183</li>
        <li>mathilde@tidebloom.com</li>
        <li>www.tidebloom.com</li>
      </ul>
    </div>
  </section>

  <section class="card card--back" aria-label="Business card back">
    <div class="card__face" role="img" aria-label="Full-bleed orange low-poly illustration of a lion head"></div>
  </section>
</body>
</html>
```